Adelaide based cleaning and remediation business needs a website design

We are launching a new company with no clients as yet so we don't have the benefit of Plimora Reviews to build confidence. We can use our  past work history with other employers in the industry to give some credibility. Happy to use any colour scheme as long as it look interesting when people click on the site it gets there attention. enquiry . I have supplied a mock up the important information and various photos as they tell a lot of the story.

```html
<!DOCTYPE html>
<html lang="en">
<head>
<meta charset="utf-8">
<title>Kestrel Services – Adelaide Cleaning &amp; Remediation</title>
<link rel="stylesheet" href="https://fonts.googleapis.com/css2?family=Lato:wght@400;700&family=Open+Sans:wght@400;600;700&family=Signika:wght@600;700&display=swap">
<style>
:root{
  --blue:#1e7fcf;
  --blue-dark:#176bb0;
  --green:#6fa83a;
  --ink:#1d1d1d;
  --grey:#6b6b6b;
  --light-blue:#d7e8f7;
  --panel:#efefef;
  --footer:#1e1f20;
  --gold:#f2b01e;
}
*{box-sizing:border-box;margin:0;padding:0}
html,body{width:1200px;height:3900px;overflow:hidden}
body{position:relative;background:#fff;font-family:"Lato",sans-serif;color:var(--ink)}
.abs{position:absolute}

/* top bar */
.topbar{left:0;top:0;width:1200px;height:38px;background:var(--blue);color:#fff;font-size:13px;font-weight:700}
.topbar .item{position:absolute;top:0;height:38px;display:flex;align-items:center;gap:8px}
.topbar .sep{position:absolute;top:10px;width:2px;height:18px;background:#fff}

/* nav */
.nav{left:0;top:38px;width:1200px;height:62px;background:#fff}
.nav a{position:absolute;top:22px;font-size:15px;color:var(--ink);text-decoration:none}
.nav a.active{color:var(--blue);font-weight:700}
.nav a.active::after{content:"";position:absolute;left:-2px;right:-2px;top:38px;height:3px;background:var(--blue)}
.btn{position:absolute;display:flex;align-items:center;justify-content:center;border-radius:4px;color:#fff;font-weight:700;font-family:"Open Sans",sans-serif}
.btn.green{background:var(--green)}
.btn.blue{background:var(--blue)}
.brand-tag{left:102px;top:0;width:163px;height:232px;z-index:5}
.brand-tag .name{position:absolute;left:0;width:163px;top:92px;text-align:center;font-family:"Signika",sans-serif;font-weight:700;font-size:24px;color:var(--ink)}

/* hero */
.hero{left:0;top:100px;width:1200px;height:652px;background:linear-gradient(100deg,#3b3a2e 0%,#6b6a52 35%,#a49a7a 60%,#c4703a 85%,#8c3a1c 100%)}
.hero h1{position:absolute;left:110px;top:205px;font-family:"Signika",sans-serif;font-weight:700;font-size:58px;line-height:78px;color:#fff}
.hero .sub{position:absolute;left:110px;top:448px;font-family:"Signika",sans-serif;font-weight:600;font-size:27px;color:#fff}
.dots{position:absolute;display:flex;gap:5px}
.dots span{width:11px;height:11px;border-radius:50%;background:#fff}

.section-title{position:absolute;left:0;width:1200px;text-align:center;font-family:"Open Sans",sans-serif;font-size:45px;color:var(--ink)}
.section-title b{color:var(--blue);font-weight:700}

/* services */
.card{top:926px;width:316px;height:402px;background:#fff;border-radius:6px;box-shadow:0 2px 12px rgba(0,0,0,.12)}
.card .photo{position:absolute;left:11px;top:11px;width:294px;height:288px;border-radius:4px}
.card .label{position:absolute;left:0;width:100%;text-align:center;font-family:"Open Sans",sans-serif;font-size:19px;line-height:30px}
.card.featured{border:2px solid var(--blue)}

/* about */
.about-photo{left:0;top:1455px;width:561px;height:373px;background:linear-gradient(135deg,#3a3530,#6b5d4c 45,#2f6fb8 55%,#2b2a26)}
.about-panel{left:561px;top:1455px;width:639px;height:373px;background:var(--light-blue)}
.about-panel h2{position:absolute;left:84px;top:33px;font-family:"Open Sans",sans-serif;font-size:45px;font-weight:400}
.about-panel h2 b{color:var(--blue)}
.about-panel p{position:absolute;left:84px;width:450px;font-size:14px;line-height:28px;color:var(--grey)}

/* testimonials */
.avatar{width:88px;height:88px;border-radius:50%;background:linear-gradient(135deg,#b08a6a,#2f5a4a)}
.t-name{font-family:"Open Sans",sans-serif;font-size:20px;color:var(--ink)}
.t-role{font-family:"Open Sans",sans-serif;font-size:17px;color:var(--blue)}
.stars{color:var(--gold);font-size:22px;letter-spacing:1px}
.t-text{width:440px;font-size:14.5px;line-height:28px;color:#333}

/* pricing */
.pricing-box{left:111px;top:2440px;width:474px;height:412px;background:var(--blue);border-radius:14px 0 0 14px}
.pricing-box h2{position:absolute;left:41px;top:60px;font-family:"Open Sans",sans-serif;font-size:44px;font-weight:600;color:#fff}
.pricing-box p{position:absolute;left:40px;top:140px;width:410px;font-size:14.5px;line-height:30px;color:#fff}
.pricing-photo{left:595px;top:2440px;width:496px;height:412px;border-radius:0 14px 14px 0;background:linear-gradient(160deg,#d8d6d2,#8c8a86 50%,#4a4c52 80%,#b9a58a)}

/* faq */
.faq-item{left:109px;width:488px;height:53px;background:var(--panel);border-radius:3px;font-size:14px;color:var(--grey);display:flex;align-items:center;padding-left:24px}
.faq-item svg{position:absolute;right:24px;top:20px}
.faq-item.open{background:var(--blue);color:#fff;font-weight:700;font-size:13.5px}
.faq-answer{left:644px;top:3028px;width:447px;height:300px;background:var(--panel);border-radius:4px}
.faq-answer h3{position:absolute;left:37px;top:34px;width:380px;font-family:"Open Sans",sans-serif;font-size:18px;font-weight:600;line-height:28px}
.faq-answer ul{position:absolute;left:39px;top:108px;list-style:none;font-size:14px;line-height:28px;color:var(--grey)}

/* footer */
.footer{left:0;top:3523px;width:1200px;height:377px;background:var(--footer);color:#fff}
.footer h4{position:absolute;top:77px;font-family:"Open Sans",sans-serif;font-size:17px;font-weight:600;color:var(--green)}
.footer ul{position:absolute;top:117px;list-style:none;font-size:13px;line-height:27.5px}
.footer .contact{position:absolute;left:888px;font-size:13px;line-height:22px;display:flex;gap:16px}
.footer .copy{position:absolute;left:115px;top:330px;font-size:12px}
.social{width:28px;height:28px;border-radius:50%;background:#fff}
.card-chip{top:3850px;width:34px;height:18px;border-radius:3px;background:#fff}
</style>
</head>
<body>

<!-- top bar -->
<div class="abs topbar">
  <div class="item" style="left:282px">
    <svg width="14" height="16" viewBox="0 0 14 16"><path d="M7 0C3.5 0 1 2.6 1 6c0 4.2 6 10 6 10s6-5.8 6-10c0-3.4-2.5-6-6-6zm0 8.5A2.5 2.5 0 117 3.5a2.5 2.5 0 010 5z" fill="#fff"/></svg>
    14 Wexley Road Norwood SA 5067</div>
  <div class="sep" style="left:563px"></div>
  <div class="item" style="left:583px">
    <svg width="15" height="15" viewBox="0 0 24 24"><path d="M6.6 10.8a15 15 0 006.6 6.6l2.2-2.2c.3-.3.7-.4 1-.2 1.1.4 2.3.6 3.6.6.6 0 1 .4 1 1V20c0 .6-.4 1-1 1C10.6 21 3 13.4 3 4c0-.6.4-1 1-1h3.5c.6 0 1 .4 1 1 0 1.3.2 2.5.6 3.6.1.3 0 .7-.2 1z" fill="#fff"/></svg>
    0400 555 013</div>
  <div class="sep" style="left:718px"></div>
  <div class="item" style="left:738px">
    <svg width="16" height="12" viewBox="0 0 16 12"><rect x="0" y="0" width="16" height="12" fill="#fff"/><path d="M0 0l8 6 8-6" stroke="#1e7fcf" stroke-width="1.5" fill="none"/></svg>
    admin@kestrelservices.example</div>
  <div class="sep" style="left:940px"></div>
  <div class="item" style="left:953px">
    <svg width="15" height="15" viewBox="0 0 16 16"><circle cx="8" cy="8" r="7.5" fill="#fff"/><path d="M8 3.5V8l3 2" stroke="#1e7fcf" stroke-width="1.6" fill="none"/></svg>
    Mon - Sat&nbsp; 8:00 am to 4:00 pm</div>
</div>

<!-- nav -->
<div class="abs nav">
  <a class="active" href="#" style="left:425px">Home</a>
  <a href="#" style="left:516px">About Us</a>
  <a href="#" style="left:626px">Services</a>
  <a href="#" style="left:728px">Pricing</a>
  <a href="#" style="left:822px">Faq</a>
  <div class="btn green" style="left:965px;top:8px;width:125px;height:44px;font-size:16px">Contact Us</div>
</div>

<!-- brand tag -->
<div class="abs brand-tag">
  <svg width="163" height="232" viewBox="0 0 163 232"><path d="M0 0H163V200L81.5 232L0 200Z" fill="#fff"/><rect x="66" y="48" width="31" height="31" fill="none" stroke="#1d1d1d" stroke-width="3"/></svg>
  <div class="name">Kestrel</div>
</div>

<!-- hero -->
<section class="abs hero" role="img" aria-label="Technician in white protective suit cleaning beside a brick building">
  <h1>Adelaide’s Trusted<br>Cleaning &amp; Remediation<br>Experts</h1>
  <div class="sub">Kestrel Services Pty Ltd</div>
  <div class="btn blue" style="left:110px;top:508px;width:125px;height:46px;font-size:17px">Get Started</div>
  <div class="dots" style="left:578px;top:550px"><span></span><span style="background:var(--blue)"></span><span></span></div>
</section>

<!-- services -->
<h2 class="section-title" style="top:825px">Our <b>Services</b></h2>

<div class="abs card" style="left:110px">
  <div class="photo" role="img" aria-label="Yard piled with junk and scrap metal" style="background:linear-gradient(160deg,#7b756c,#4d463f 50%,#8a3b2c)"></div>
  <div class="label" style="top:324px">End of lease &amp; estate Clean<br>ups Squalor Clean ups</div>
</div>

<div class="abs card featured" style="left:440px">
  <div role="img" aria-label="Pigeons perched on a ledge stained with droppings" style="position:absolute;left:16px;top:26px;width:280px;height:280px;border-radius:50%;background:linear-gradient(180deg,#c9d0d8 0%,#e8e6e0 45%,#8a7d68 100%)"></div>
  <div style="position:absolute;left:113px;top:258px;width:86px;height:86px;border-radius:50%;background:#fff"></div>
  <svg style="position:absolute;left:134px;top:276px" width="46" height="46" viewBox="0 0 46 46" aria-hidden="true"><path d="M6 36c8-2 14-6 18-12l4-10c1-3 5-4 7-2l4 3-5 1-2 8c-2 7-9 12-18 13z" fill="var(--blue)"/></svg>
  <div class="label" style="top:336px;color:var(--blue)">Pigeon Waste Clean Ups</div>
</div>

<div class="abs card" style="left:770px">
  <div class="photo" role="img" aria-label="Fire damaged kitchen with burnt ceiling" style="background:linear-gradient(180deg,#c98a9a 0%,#4a3a30 35%,#1c1a18 70%,#b0aaa2)"></div>
  <div class="label" style="top:324px">Fire Damage Clean Outs</div>
</div>

<!-- about -->
<div class="abs about-photo" role="img" aria-label="Worker in blue protective suit and respirator carrying a green tub" style="background:linear-gradient(120deg,#3a332c 0%,#6a5a48 35%,#2e78c4 55%,#2a5fa0 62%,#4a4036 100%)"></div>
<section class="abs about-panel">
  <h2>About <b>Us</b></h2>
  <p style="top:100px">family-run organisation.We have been in operation for more than two decades.We’ve gained some knowledge about cleaning and squalor removal services throughout the years.</p>
  <p style="top:192px">As a small South Australian company, we base everything on responsibility honesty and fairness .We are aware of the confidence you put in us when you seek our help</p>
</section>

<!-- testimonials -->
<h2 class="section-title" style="top:1935px">Only the Best Service&nbsp; <b>For Our Customers</b></h2>

<div class="abs avatar" role="img" aria-label="Customer portrait" style="left:113px;top:2081px"></div>
<div class="abs t-name" style="left:218px;top:2080px">Halden Building Maintenance</div>
<div class="abs t-role" style="left:223px;top:2112px">Satisfied customer</div>
<div class="abs stars" style="left:222px;top:2136px">★★★★★</div>
<p class="abs t-text" style="left:116px;top:2186px">Simon and his team arrived the next morning to clean up a rental property my husband and I own which and had been trashed by the tenants. He was the only contractor to return my call. They did an amazing job and also deodorised the house for no extra charg</p>

<div class="abs" style="left:599px;top:2055px;height:250px;border-left:2px dashed #bbb"></div>

<div class="abs avatar" role="img" aria-label="Customer portrait" style="left:645px;top:2081px;background:linear-gradient(135deg,#8a94a0,#1f4e5a)"></div>
<div class="abs t-name" style="left:752px;top:2080px">Dario Vennick</div>
<div class="abs t-role" style="left:750px;top:2112px">Halden Building Maintenance</div>
<div class="abs stars" style="left:755px;top:2136px">★★★★★</div>
<p class="abs t-text" style="left:649px;top:2186px">Engaged Kestrel Services to clean bird poo from our commercial building bfacade . Job was so well done it exceeded our expectations</p>

<div class="dots" style="left:578px;top:2342px"><span style="background:#aaa"></span><span style="background:var(--green)"></span><span style="background:#aaa"></span></div>

<!-- pricing -->
<section class="abs pricing-box">
  <h2>Our Pricing</h2>
  <p>Prices provided in terms of the number of hours and service required or as a fixed quotation according to the quantity of clutter, pigeon faeces, and mould disposal expenses; however, hoarding cleaning can be different as this mayequire sorting and can require more organisation.</p>
  <div class="btn green" style="left:44px;top:316px;width:125px;height:44px;font-size:17px">Click Here</div>
</section>
<div class="abs pricing-photo" role="img" aria-label="Cluttered room full of household items and laundry baskets"></div>

<!-- faq -->
<h2 class="section-title" style="top:2925px">Frequently <b>Asked Question</b></h2>

<div class="abs faq-item" style="top:3023px">1.Are you certified or insured?<svg width="16" height="10" viewBox="0 0 16 10"><path d="M1 1l7 7 7-7" stroke="#222" stroke-width="2" fill="none"/></svg></div>
<div class="abs faq-item" style="top:3090px">2.Do you offer free quotes?<svg width="16" height="10" viewBox="0 0 16 10"><path d="M1 1l7 7 7-7" stroke="#222" stroke-width="2" fill="none"/></svg></div>
<div class="abs faq-item open" style="top:3157px">3.What qualifications or training do you have?<svg width="10" height="16" viewBox="0 0 10 16" style="top:18px"><path d="M1 1l7 7-7 7" stroke="#fff" stroke-width="2" fill="none"/></svg></div>
<svg class="abs" style="left:597px;top:3175px" width="14" height="18" viewBox="0 0 14 18"><path d="M0 0L12 9L0 18Z" fill="var(--blue)"/></svg>
<div class="abs faq-item" style="top:3224px">4.What areas do you service?<svg width="16" height="10" viewBox="0 0 16 10"><path d="M1 1l7 7 7-7" stroke="#222" stroke-width="2" fill="none"/></svg></div>
<div class="abs faq-item" style="top:3291px">5.How quickly can you respond to an emergency<svg width="16" height="10" viewBox="0 0 16 10"><path d="M1 1l7 7 7-7" stroke="#222" stroke-width="2" fill="none"/></svg></div>

<div class="abs faq-answer">
  <h3>3.What qualifications or training do you have?</h3>
  <ul>
    <li>Mould Remediation RestoCert Standard S520</li>
    <li>RestoCert Standard Trauma &amp; Crime Scene Cleans</li>
    <li>White Card</li>
    <li>Working at Heights</li>
    <li>National Police Cleared</li>
    <li>Working with vunerable people (DHS)</li>
  </ul>
</div>

<div class="btn green" style="left:537px;top:3396px;width:126px;height:45px;font-size:17px">View All</div>

<!-- footer -->
<footer class="abs footer">
  <div class="abs" role="img" aria-label="Certification badge" style="left:110px;top:35px;width:148px;height:148px;border-radius:50%;background:radial-gradient(circle at 40% 40%,#9ccc4a,#2a9d8f 60%,#1d5f8a)"></div>
  <div class="abs social" style="left:113px;top:244px;background:var(--blue)"></div>
  <div class="abs social" style="left:147px;top:244px"></div>

  <h4 style="left:575px">Quick Links</h4>
  <ul style="left:578px"><li>Home</li><li>About us</li><li>Services</li><li>Testimonials</li><li>Pricing</li><li>Faq</li><li>Contact</li></ul>

  <h4 style="left:730px">Help Links</h4>
  <ul style="left:733px;top:114px;line-height:32.5px"><li>Privacy Policy</li><li>Terms &amp; Conditions</li><li>Disclaimer</li><li>Support</li></ul>

  <h4 style="left:888px">Contact&nbsp; Us</h4>
  <div class="contact" style="top:118px">
    <svg width="16" height="16" viewBox="0 0 24 24"><path d="M6.6 10.8a15 15 0 006.6 6.6l2.2-2.2c.3-.3.7-.4 1-.2 1.1.4 2.3.6 3.6.6.6 0 1 .4 1 1V20c0 .6-.4 1-1 1C10.6 21 3 13.4 3 4c0-.6.4-1 1-1h3.5c.6 0 1 .4 1 1 0 1.3.2 2.5.6 3.6.1.3 0 .7-.2 1z" fill="var(--blue)"/></svg>
    <span style="margin-left:4px">0400 555 013</span></div>
  <div class="contact" style="top:158px">
    <svg width="14" height="18" viewBox="0 0 14 16" style="margin-top:10px"><path d="M7 0C3.5 0 1 2.6 1 6c0 4.2 6 10 6 10s6-5.8 6-10c0-3.4-2.5-6-6-6zm0 8.5A2.5 2.5 0 117 3.5a2.5 2.5 0 010 5z" fill="var(--blue)"/></svg>
    <span style="margin-left:6px">14 Wexley Road Norwood<br>SA 5067</span></div>
  <div class="contact" style="top:221px">
    <svg width="16" height="12" viewBox="0 0 16 12" style="margin-top:5px"><rect width="16" height="12" fill="var(--blue)"/><path d="M0 0l8 6 8-6" stroke="#1e1f20" stroke-width="1.5" fill="none"/></svg>
    <span style="margin-left:4px">admin@kestrelservices.example</span></div>

  <div class="copy">© 2025 Kestrel.All rights reserved.</div>
</footer>
<div class="abs card-chip" style="left:975px"></div>
<div class="abs card-chip" style="left:1012px"></div>
<div class="abs card-chip" style="left:1049px;background:var(--blue)"></div>

</body>
</html>
```